Vantiqo custom business card design

Need a authentic, innovative business card design for a new mobile app business. I am uploading a few screen images from our app for you to view. I would like app design theme to match business card design. I can also send logo images.

```html
<!DOCTYPE html>
<html lang="en">
<head>
<meta charset="utf-8">
<title>Vantiqo business card</title>
<link href="https://fonts.googleapis.com/css2?family=Montserrat:wght@700;800&family=Open+Sans:wght@400;600&display=swap" rel="stylesheet">
<style>
  :root {
    --purple: #5d0b8f;
    --purple-soft: #6b1a9e;
    --card-light: #e6e6e8;
    --ink: #1d1d1f;
    --rule: #a9a9ad;
    --stage: #4a4a4d;
    --white: #ffffff;
  }
  * { margin: 0; padding: 0; box-sizing: border-box; }
  html, body {
    width: 1200px; height: 896px; overflow: hidden;
    background: var(--stage);
  }
  .canvas {
    width: 1200px; height: 896px;
    display: flex; flex-direction: column;
    align-items: center; justify-content: center; gap: 40px;
  }
  .card {
    position: relative;
    width: 680px; height: 388px;
    overflow: hidden;
    box-shadow: 0 6px 18px rgba(0,0,0,0.35);
  }

  /* Front */
  .card-front { background: var(--card-light); }
  .card-front .base-band {
    position: absolute; left: 0; right: 0; bottom: 0; height: 18px;
    background: var(--purple);
  }
  .person { position: absolute; left: 46px; top: 92px; }
  .person-name {
    font-family: "Montserrat", sans-serif; font-weight: 800;
    font-size: 26px; letter-spacing: 0.5px; text-transform: uppercase;
    color: var(--purple); line-height: 1.1;
  }
  .person-role {
    font-family: "Open Sans", sans-serif; font-size: 16px;
    color: var(--ink); margin-top: 2px;
  }
  .contacts { position: absolute; left: 46px; top: 170px; list-style: none; }
  .contacts li {
    display: flex; align-items: center; gap: 8px;
    font-family: "Open Sans", sans-serif; font-size: 16px;
    color: var(--ink); line-height: 24px;
  }
  .contacts svg { width: 13px; height: 13px; fill: var(--purple); flex: none; }
  .divider {
    position: absolute; left: 46px; right: 46px; top: 256px;
    height: 1px; background: var(--rule);
  }
  .brand-lockup {
    position: absolute; right: 58px; top: 170px;
    display: flex; align-items: center; gap: 10px;
  }
  .brand-dot { width: 30px; height: 30px; border-radius: 50%; background: var(--purple); }
  .brand-name {
    font-family: "Montserrat", sans-serif; font-weight: 800;
    font-size: 38px; color: var(--ink); letter-spacing: 0.5px;
  }
  .address {
    position: absolute; right: 58px; top: 272px; text-align: right;
    font-family: "Open Sans", sans-serif; font-size: 16px;
    color: var(--ink); line-height: 22px;
  }

  /* Back */
  .card-back { background: var(--purple); }
  .card-back .soft-circle {
    position: absolute; width: 420px; height: 420px; border-radius: 50%;
    left: 130px; top: -16px; background: var(--purple-soft); opacity: 0.55;
  }
  .card-back .brand-name-reversed {
    position: absolute; left: 0; right: 0; top: 50%; transform: translateY(-50%);
    text-align: center;
    font-family: "Montserrat", sans-serif; font-weight: 800;
    font-size: 64px; color: var(--white); letter-spacing: 1px;
  }
</style>
</head>
<body>
<main class="canvas">
  <section class="card card-front" aria-label="Card front">
    <div class="person">
      <h1 class="person-name">Dorian Kell</h1>
      <p class="person-role">Managing Director</p>
    </div>
    <ul class="contacts">
      <li>
        <svg viewBox="0 0 16 16" aria-hidden="true"><path d="M3 1h3l1.5 4-2 1.3a9 9 0 0 0 4.2 4.2L11 8.5 15 10v3a2 2 0 0 1-2 2A12 12 0 0 1 1 3a2 2 0 0 1 2-2z"/></svg>
        055-210 874 336
      </li>
      <li>
        <svg viewBox="0 0 16 16" aria-hidden="true"><path d="M4.5 0h7A1.5 1.5 0 0 1 13 1.5v13a1.5 1.5 0 0 1-1.5 1.5h-7A1.5 1.5 0 0 1 3 14.5v-13A1.5 1.5 0 0 1 4.5 0zM5 2v10h6V2zm3 11a1 1 0 1 0 0 2 1 1 0 0 0 0-2z"/></svg>
        055-210 874 336
      </li>
      <li>
        <svg viewBox="0 0 16 16" aria-hidden="true"><path d="M0 3h16v10H0zm1.5 1.4V12h13V4.4L8 9z"/></svg>
        hello@vantiqo.app
      </li>
    </ul>
    <div class="brand-lockup">
      <span class="brand-dot" aria-hidden="true"></span>
      <span class="brand-name">Vantiqo</span>
    </div>
    <div class="divider"></div>
    <p class="address">48 Larkfield Row,<br>Northbay, 204718</p>
    <div class="base-band"></div>
  </section>

  <section class="card card-back" aria-label="Card back">
    <div class="soft-circle" aria-hidden="true"></div>
    <p class="brand-name-reversed">Vantiqo</p>
  </section>
</main>
</body>
</html>
```